Redesign of Grown Builder of BRIXO Weblog.

I'm an Grown Builder of BRIXO (GBOB), and I'm the person behind a small, off-the-beaten-path fan site, built using PageLoom.

The existing site is at http://quarvelnook.example. As you can see, it could use an infinitely better design!

My site was originally for reviews of BRIXO sets, and had extended to include general commentary and a small gallery of models I've built and a cast of characters. It's particularly known for my opinions and perspective on the world of BRIXO, and as such isn't necessarily child friendly.
While keeping existing content, the new version of the site will focus more on video content from my ClipHarbor channel.

In contrast to the current site, I'm looking for a light design that makes use of a few muted, low saturation colours, whilst remaining clean and relatively simple. The logo is part of the site's identity and should serve as inspiration for the design.
The content pages would keep the thin floating menu, and the content area would be no more than 1200 pixels wide.
Though it's a BRIXO fan site, I would like to avoid overt references to BRIXO elements. Other that that, you're more than welcome to use your creative license with the design.

In addition to the home, blog and post pages, I would also like a "placeholder" page that can be adapted for different page types. I will be building the theme from the designs, so don't worry about doing any coding.
You don't have to provide them all at once at this stage: I would suggest submitting either the home page or post page.

The final design should communicate "this is MY corner of the web", but above all else that it's about creativity and self-expression.

If you have any questions, please get in touch!
Updates

Target Market(s)

People interested in BRIXO in general, 12 and up.

Industry/Entity Type

Adult

Number of Pages Required

4 page

Font styles to use
Sans Serif
Decorative
Other font styles liked:
• Qhytsdakx

Requirements
Must have
• The tagline "Make It Yours".
• I'm keeping the font/fount used for headings (Qhytsdakx); I'm open to suggestions for the body text.
Should not have
• Overt references to BRIXO or BRIXO elements.

```html
<!DOCTYPE html>
<html lang="en">
<head>
<meta charset="utf-8">
<title>Quarvelnook Commentary</title>
<link rel="stylesheet" href="https://fonts.googleapis.com/css2?family=Oxanium:wght@400;500;600&family=Open+Sans:wght@400;600;700&display=swap">
<style>
:root{
  --ink:#1c1c1c;
  --text:#555;
  --muted:#8a8a8a;
  --line:#dcdcdc;
  --page:#f7f7f7;
  --white:#fff;
  --blue:#2a8fc9;
  --green:#5cc97b;
  --red:#d9443b;
  --tab:#e3e3e3;
  --footer:#0c0c0c;
  --orange:#f26a2a;
  --date:#a3a3a3;
  --button:#3a5fc0;
}
*{box-sizing:border-box;margin:0;padding:0}
html,body{width:1200px;height:2620px;overflow:hidden}
body{position:relative;background:var(--page);font-family:"Open Sans",Arial,sans-serif;color:var(--text);font-size:13px}
.abs{position:absolute}

/* header */
.site-header{position:absolute;left:0;top:0;width:1200px;height:70px;background:var(--white)}
.brand{position:absolute;left:128px;top:0;height:70px;display:flex;align-items:center;gap:9px}
.brand-mark{width:20px;height:20px;background:var(--ink)}
.brand-name{font-family:"Oxanium",sans-serif;font-weight:600;font-size:20px;color:var(--ink)}
.tagline{position:absolute;left:316px;top:23px;font-family:"Oxanium",sans-serif;font-weight:600;font-size:20px;letter-spacing:1px;color:var(--ink);text-transform:uppercase}
.nav a{position:absolute;top:22px;height:36px;line-height:36px;font-family:"Oxanium",sans-serif;font-size:13px;letter-spacing:2px;color:var(--ink);text-decoration:none}
.nav a.active{background:var(--blue);color:var(--white);padding:0 18px;top:20px}

/* hero */
.hero{position:absolute;left:0;top:70px;width:1200px;height:310px;background:linear-gradient(90deg,#2a2a2a,#3d3b3b 45%,#5a2a2a 70%,#3a3a3a)}
.hero-shade{position:absolute;inset:0;background:rgba(0,0,0,.35)}
.hero h1{position:absolute;left:0;width:1200px;top:118px;text-align:center;font-family:"Oxanium",sans-serif;font-weight:500;font-size:44px;letter-spacing:7px;color:var(--white)}
.hero p{position:absolute;left:0;width:1200px;top:184px;text-align:center;font-size:12.5px;line-height:17px;color:var(--white)}

/* post */
.post-title{left:84px;top:426px;font-family:"Oxanium",sans-serif;font-weight:400;font-size:27px;color:var(--ink)}
.post-date{left:690px;top:432px;width:72px;height:24px;background:var(--date);color:var(--white);font-family:"Oxanium",sans-serif;font-size:11px;text-align:center;line-height:24px;letter-spacing:1px}
.byline{left:84px;top:466px;font-size:12px}
.byline span{color:var(--red)}
.meta{left:84px;top:500px;width:678px;height:26px;border-bottom:1px solid var(--line);display:flex;gap:22px;font-size:12px;color:#666}
.meta i{display:inline-block;width:13px;height:11px;border:1.5px solid #777;margin-right:6px;vertical-align:-1px;border-radius:2px}
.video{left:84px;top:542px;width:678px;height:445px;background:linear-gradient(135deg,#4a4a4a,#6e6a64 40%,#3b3b3b 75%,#2a2a2a)}
.video-bar{position:absolute;left:0;bottom:0;width:678px;height:44px;background:rgba(0,0,0,.75)}
.progress{position:absolute;left:10px;top:8px;width:658px;height:4px;background:#666}
.progress b{display:block;width:375px;height:4px;background:var(--red)}
.video-time{position:absolute;left:118px;top:20px;font-size:10px;color:#ddd}
.post-body{left:84px;top:1025px;width:678px;font-size:12.5px;line-height:22px;color:#666;text-align:justify}
.section-label{font-family:"Oxanium",sans-serif;font-size:16px;color:var(--ink)}
.share{left:84px;top:1162px;display:flex;gap:8px}
.share span{height:26px;border:1px solid var(--line);background:var(--white);font-size:9.5px;color:#555;padding:0 8px 0 0;display:flex;align-items:center;gap:6px}
.share span i{width:24px;height:24px;display:block}
.rule{left:84px;width:678px;height:1px;background:var(--line)}
.related{top:1295px;width:324px;display:flex;gap:16px}
.related .thumb{width:146px;height:114px;flex:none;border:2px solid #bbb}
.related h4{font-family:"Oxanium",sans-serif;font-weight:400;font-size:13.5px;color:var(--ink)}
.related small{font-size:12px;color:var(--muted)}

/* comments */
.comments-count{left:84px;top:1490px;font-weight:700;font-size:14px;color:var(--ink)}
.star{left:716px;top:1490px;color:#f2b600;font-size:16px}
.zero{left:740px;top:1490px;width:20px;height:18px;background:#ddd;font-size:11px;text-align:center;line-height:18px}
.avatar{background:#c8c8c8}
.comment-input{left:130px;top:1527px;width:632px;height:32px;border:1px solid #bbb;background:var(--white);font-size:11px;color:#aaa;padding:8px 10px}
.tabs{left:84px;top:1582px;width:678px;height:22px;border-bottom:1px solid var(--line);font-size:10px;color:#555}
.tabs span{position:absolute;top:0}
.tabs .on{border-bottom:2px solid #555;padding-bottom:5px}
.comment{width:678px}
.comment .who{font-size:11px;font-weight:700;color:#444}
.comment .who em{font-style:normal;font-weight:400;color:#999;font-size:10px}
.comment p{font-size:11.5px;color:#555;margin-top:2px}
.comment .acts{font-size:9.5px;color:#999;margin-top:3px}
.pager{top:1878px;font-family:"Oxanium",sans-serif;font-size:16px;letter-spacing:3px;color:#555}

/* sidebar */
.search{left:788px;top:432px;width:325px;height:33px;border:1px solid #bbb;background:var(--white);font-family:"Oxanium",sans-serif;font-size:11px;letter-spacing:2px;color:#888;padding:9px 12px}
.side-head{left:788px;width:325px;border-bottom:1px solid var(--line);font-family:"Oxanium",sans-serif;font-size:20px;letter-spacing:3px;color:var(--ink);padding-bottom:10px;padding-left:20px}
.side-head::before{content:"";position:absolute;left:0;top:9px;width:7px;height:7px;background:var(--green)}
.year{left:788px;width:325px;height:32px;background:var(--tab);font-family:"Oxanium",sans-serif;font-size:15px;color:#555;padding:6px 16px}
.year.open{background:var(--green);color:var(--white)}
.year svg{position:absolute;right:14px;top:11px}
.months{left:805px;top:604px;font-size:11px;line-height:21px;color:#999}
.months b{font-weight:400;color:var(--blue)}
.side-item{left:788px;width:325px;height:77px;display:flex;gap:16px}
.side-item .thumb{width:77px;height:58px;flex:none;border:2px solid #bbb}
.side-item h4{font-family:"Oxanium",sans-serif;font-weight:400;font-size:12.5px;line-height:18px;color:var(--ink);margin-top:8px}
.side-item small{font-size:11.5px;color:var(--muted)}
.ad{left:805px;width:296px}
.ad-studio{left:805px;top:1775px;width:296px;display:flex;align-items:center;gap:8px;font-size:22px;font-weight:600;color:var(--ink)}
.ad-studio i{width:22px;height:22px;background:var(--orange);border-radius:50%}

/* footer */
.site-footer{position:absolute;left:0;top:2067px;width:1200px;height:553px;background:var(--footer);color:var(--white)}
.foot-head{position:absolute;font-family:"Oxanium",sans-serif;font-size:17px;letter-spacing:3px;color:var(--white)}
.grid{position:absolute;display:grid;grid-template-columns:repeat(5,56px);gap:10px 11px}
.grid span{height:54px}
.tweet{position:absolute;left:444px;width:320px;font-size:12px;line-height:16px;color:#eee;padding-left:22px}
.tweet::before{content:"";position:absolute;left:0;top:3px;width:12px;height:10px;border-radius:50%;background:var(--blue)}
.tweet a{color:var(--blue);text-decoration:none}
.about{position:absolute;left:791px;top:94px;width:322px;font-size:12px;line-height:16px;color:#eee;text-align:justify}
.read-more{position:absolute;left:791px;top:176px;width:102px;height:27px;background:var(--button);font-family:"Oxanium",sans-serif;font-size:10px;letter-spacing:1.5px;line-height:27px;text-align:center;color:var(--white)}
.partner{position:absolute;left:791px;width:322px;height:75px;border:2px solid #ddd;display:flex;align-items:center;justify-content:center;gap:10px;font-size:24px;font-weight:600}
.partner i{width:20px;height:20px;background:var(--white)}
.foot-mark{position:absolute;left:90px;top:481px;display:flex;align-items:center;gap:8px;font-family:"Oxanium",sans-serif;font-size:16px;font-weight:600}
.foot-mark i{width:22px;height:22px;background:var(--white)}
.copy{position:absolute;left:250px;top:478px;font-size:11px;line-height:16px;color:#777}
.copy b{color:#ddd;font-weight:400}
</style>
</head>
<body>

<header class="site-header">
  <div class="brand"><span class="brand-mark"></span><span class="brand-name">Quarvelnook</span></div>
  <div class="tagline">Make It Yours</div>
  <nav class="nav">
    <a class="active" style="left:562px">Commentary</a>
    <a style="left:712px">Reviews</a>
    <a style="left:813px">MOCs</a>
    <a style="left:890px">Cast</a>
    <a style="left:961px">About</a>
    <a style="left:1045px">Contact</a>
  </nav>
</header>

<section class="hero" role="img" aria-label="Dimmed photo of a building figure in front of a red and black backdrop">
  <div class="hero-shade"></div>
  <h1>QUARVELNOOK'S COMMENTARY</h1>
  <p>Quarvelnook has an opinion on just about everything, and whenever the mood is right we offer our views – good or bad – right here.<br>Please note that Quarvelnook does not report on, use or respect any leaked or confidential material.</p>
</section>

<main>
  <h2 class="abs post-title">Nam eget dui.</h2>
  <div class="abs post-date">10 / 24 / 16</div>
  <div class="abs byline">by <span>Quarvelnook</span></div>
  <div class="abs meta"><span><i></i>3</span><span><i style="border-radius:50%"></i>322</span><span><i style="width:9px"></i>Miscellaneous</span></div>

  <div class="abs video" role="img" aria-label="Video still of a building-figure family with a baby and a wheelchair">
    <svg class="abs" style="left:301px;top:178px" width="76" height="76" viewBox="0 0 76 76"><circle cx="38" cy="38" r="38" fill="#fff"/><path d="M30 22 L56 38 L30 54 Z" fill="#e0383b"/></svg>
    <div class="video-bar">
      <div class="progress"><b></b></div>
      <svg class="abs" style="left:14px;top:18px" width="80" height="16" viewBox="0 0 80 16" fill="#fff"><rect x="0" y="2" width="4" height="12"/><rect x="7" y="2" width="4" height="12"/><path d="M26 2 L34 8 L26 14 Z"/><rect x="35" y="2" width="2" height="12"/><path d="M52 5 H56 L61 1 V15 L56 11 H52 Z"/></svg>
      <span class="video-time">0:35 / 2:25</span>
      <svg class="abs" style="left:548px;top:18px" width="118" height="16" viewBox="0 0 118 16" fill="#fff"><rect x="0" y="3" width="14" height="10" rx="1"/><circle cx="36" cy="8" r="6"/><circle cx="36" cy="8" r="2" fill="#222"/><rect x="56" y="3" width="16" height="10" fill="none" stroke="#fff" stroke-width="2"/><path d="M90 1 H96 V3 H92 V7 H90 Z M110 1 H116 V7 H114 V3 H110 Z M90 9 H92 V13 H96 V15 H90 Z M114 9 H116 V15 H110 V13 H114 Z" transform="translate(-6 0)"/></svg>
    </div>
  </div>

  <p class="abs post-body">Nam eget dui. Etiam rhoncus. Maecenas tempus, tellus eget condimentum rhoncus, sem quam semper libero, sit amet adipiscing sem neque sed ipsum. Maecenas tempus, tellus eget condimentum rhoncus, sem quam semper libero, sit amet adipiscing sem neque sed ipsum. Nam quam nunc, blandit vel, luctus.</p>

  <div class="abs section-label" style="left:84px;top:1117px">Like it? Share it!</div>
  <div class="abs share">
    <span><i style="background:#3b5998"></i>Friendsy</span>
    <span><i style="background:#1da1f2"></i>Chirpline</span>
    <span><i style="background:#cb2027"></i>Pinboardly</span>
    <span><i style="background:#8c8c8c"></i>Snapstream</span>
    <span><i style="background:#e52d27"></i>ClipHarbor</span>
    <span><i style="background:#777"></i>Circlesy</span>
    <span><i style="background:#8cb82b"></i>E-mail</span>
  </div>
  <div class="abs rule" style="top:1220px"></div>

  <div class="abs section-label" style="left:84px;top:1256px;font-size:15px">You Might Be Interested In...</div>
  <div class="abs related" style="left:84px"><div class="thumb" role="img" aria-label="Photo of a building-figure pig character" style="background:linear-gradient(135deg,#7a4a2a,#c9853f 60%,#5a3a22)"></div><div><h4>Vivamus elementum semper nisi</h4><small>Miscellaneous</small></div></div>
  <div class="abs related" style="left:438px"><div class="thumb" role="img" aria-label="Photo of a white skeleton figure on a dark background" style="background:linear-gradient(135deg,#111,#555 50%,#1a1a1a)"></div><div><h4>Etiam ultricies nisi vel augue</h4><small>Miscellaneous</small></div></div>
  <div class="abs rule" style="top:1453px"></div>

  <div class="abs comments-count">3 comments</div>
  <div class="abs star">★</div>
  <div class="abs zero">0</div>
  <div class="abs avatar" style="left:84px;top:1527px;width:32px;height:32px"></div>
  <div class="abs comment-input">Leave a message...</div>
  <div class="abs tabs">
    <span class="on" style="left:0">Discussion ▾</span>
    <span style="left:120px">Community</span>
    <span style="left:220px">My Threadkeep</span>
    <span style="left:596px">Share ▾ &nbsp; ⚙ ▾</span>
  </div>

  <div class="abs comment" style="left:84px;top:1620px">
    <div class="avatar abs" style="left:0;top:2px;width:32px;height:32px"></div>
    <div style="margin-left:46px"><div class="who">Tom Harlow <em>• 2 days ago</em></div><p>Lorem ipsum leo amet nisl quam ut primis lacinia nisi est pharetra gravida amet urna,</p><div class="acts">12 ^ ∨ • Reply • Share</div></div>
  </div>
  <div class="abs rule" style="left:126px;width:636px;top:1682px"></div>
  <div class="abs comment" style="left:130px;top:1692px;width:632px">
    <div class="abs" style="left:0;top:2px;width:22px;height:22px;background:#222"></div>
    <div style="margin-left:34px"><div class="who">Ivo Brandt <em>• 2 days ago</em></div><p>Lorem ipsum leo amet nisl quam ut primis lacinia nisi est pharetra gravida amet urna,</p><div class="acts">12 ^ ∨ • Reply • Share</div></div>
  </div>
  <div class="abs rule" style="top:1755px"></div>
  <div class="abs comment" style="left:84px;top:1768px">
    <div class="avatar abs" style="left:0;top:2px;width:32px;height:32px"></div>
    <div style="margin-left:46px"><div class="who">Dotsmith <em>• 2 days ago</em></div><p>Lorem ipsum leo amet nisl quam ut primis lacinia nisi est pharetra gravida amet urna,</p><div class="acts">12 ^ ∨ • Reply • Share</div></div>
  </div>

  <div class="abs pager" style="left:86px">&lt;&lt; NEWER POST</div>
  <div class="abs pager" style="left:462px;width:300px;text-align:right">OLDER POST &gt;&gt;</div>
</main>

<aside>
  <div class="abs search">Search Blog
    <svg class="abs" style="right:10px;top:8px" width="16" height="16" viewBox="0 0 16 16"><circle cx="6.5" cy="6.5" r="5" fill="none" stroke="#777" stroke-width="1.5"/><path d="M10 10 L15 15" stroke="#777" stroke-width="1.5"/></svg>
  </div>

  <div class="abs side-head" style="top:502px">Archives</div>
  <div class="abs year open" style="top:562px">2016<svg width="12" height="8" viewBox="0 0 12 8"><path d="M1 1 L6 6 L11 1" fill="none" stroke="#fff" stroke-width="2"/></svg></div>
  <div class="abs months">January<br><b>February</b><br>March</div>
  <div class="abs year" style="top:674px">2015<svg width="12" height="8" viewBox="0 0 12 8"><path d="M1 1 L6 6 L11 1" fill="none" stroke="#555" stroke-width="2"/></svg></div>
  <div class="abs year" style="top:707px">2014<svg width="12" height="8" viewBox="0 0 12 8"><path d="M1 1 L6 6 L11 1" fill="none" stroke="#555" stroke-width="2"/></svg></div>
  <div class="abs year" style="top:740px">2013<svg width="12" height="8" viewBox="0 0 12 8"><path d="M1 1 L6 6 L11 1" fill="none" stroke="#555" stroke-width="2"/></svg></div>

  <div class="abs side-head" style="top:812px">Latest News</div>
  <div class="abs side-item" style="top:868px"><div class="thumb" role="img" aria-label="Photo of a figure family" style="background:linear-gradient(135deg,#c9b89a,#6a8ac0)"></div><div><h4>Mom, Dad, Baby and Wheelchair</h4><small>Miscellaneous</small></div></div>
  <div class="abs side-item" style="top:947px"><div class="thumb" role="img" aria-label="Photo of a scientist figure" style="background:linear-gradient(135deg,#5a4a20,#c9a040)"></div><div><h4>Final Thoughts on the Discovery Lab BRIXO Ideas set.</h4><small>Miscellaneous</small></div></div>
  <div class="abs side-item" style="top:1026px"><div class="thumb" role="img" aria-label="Photo of a scientist figure" style="background:linear-gradient(135deg,#5a4a20,#d0a848)"></div><div><h4>Final Thoughts on the Discovery Lab BRIXO Ideas set.</h4><small>Miscellaneous</small></div></div>

  <div class="abs side-head" style="top:1134px">Top Post</div>
  <div class="abs side-item" style="top:1193px"><div class="thumb" role="img" aria-label="Photo of collectible figures" style="background:linear-gradient(135deg,#333,#888)"></div><div><h4>QuarvelnookBest and Worst Collectible...</h4><small>Miscellaneous</small></div></div>
  <div class="abs side-item" style="top:1272px"><div class="thumb" role="img" aria-label="Photo of a figure with a helmet" style="background:linear-gradient(135deg,#3a6aa8,#e0b060)"></div><div><h4>Final Thoughts on the Discovery Lab BRIXO Ideas set.</h4><small>Miscellaneous</small></div></div>
  <div class="abs side-item" style="top:1350px"><div class="thumb" role="img" aria-label="Photo of a smiling figure" style="background:linear-gradient(135deg,#3a80c0,#f0c050)"></div><div><h4>UNDERATED for BRIXO Ideas: February 2016</h4><small>Miscellaneous</small></div></div>

  <div class="abs side-head" style="top:1455px">Ads</div>
  <div class="abs ad" style="top:1513px;height:246px;background:linear-gradient(180deg,#9fd6ef,#5fb8e6 60%,#e5a33a)" role="img" aria-label="Advertisement for Roamly travel points card"></div>
  <div class="abs ad-studio"><i></i>Tintwell Studio</div>
  <div class="abs ad" style="top:1817px;height:204px;background:linear-gradient(180deg,#c9a46a,#e7c48c 60%,#fff)" role="img" aria-label="Advertisement for Tintwell Studio e-commerce and online marketing services, www.tintwell.example"></div>
</aside>

<footer class="site-footer">
  <div class="foot-head" style="left:87px;top:50px">Snapstream Photostream</div>
  <div class="grid" style="left:87px;top:94px" role="img" aria-label="Grid of ten small photos of built models">
    <span style="background:#556"></span><span style="background:#667"></span><span style="background:#777"></span><span style="background:#333"></span><span style="background:#445"></span>
    <span style="background:#665"></span><span style="background:#555"></span><span style="background:#886"></span><span style="background:#544"></span><span style="background:#a63"></span>
  </div>
  <div class="foot-head" style="left:87px;top:244px">My BRIXO Cast</div>
  <div class="grid" style="left:87px;top:286px" role="img" aria-label="Grid of ten cast figures on orange backgrounds">
    <span style="background:var(--orange)"></span><span style="background:var(--orange)"></span><span style="background:var(--orange)"></span><span style="background:var(--orange)"></span><span style="background:var(--orange)"></span>
    <span style="background:var(--orange)"></span><span style="background:var(--orange)"></span><span style="background:var(--orange)"></span><span style="background:var(--orange)"></span><span style="background:var(--orange)"></span>
  </div>

  <div class="foot-head" style="left:444px;top:50px">@Quarvelnook</div>
  <p class="tweet" style="top:92px"><a>@WorldofFigurines</a> it took the best part of a month to organise photos from BUILDFEST 2015. #,<br>In just under a week my latest @plateforge order has arrived! Shout out to them. https://lnk.example/Vk8Xmq #,</p>
  <p class="tweet" style="top:184px"><a>@WorldofFigurines</a> it took the best part of a month to organise photos from BUILDFEST 2015. #,<br>In just under a week my latest @plateforge order has arrived! Shout out to them. https://lnk.example/Vk8Xmq #,</p>
  <p class="tweet" style="top:290px"><a>@OwenMarlow</a> @plankfan62 wha...?! #,<br>I will be at the @starhall for the Buildwise Weekend, showcasing the Mascotry. There may be a little surprise too. #,<br>Mom, Dad, Baby and Wheelchair <a>https://lnk.example/Qw2K35</a> <a>https://lnk.example/Rs0e7</a> #,</p>

  <div class="foot-head" style="left:791px;top:50px">About Me</div>
  <p class="about">Aenean vulputate eleifend tellus. Aenean leo ligula, porttitor eu, consequat vitae, eleifend ac, enim. Aliquam lorem ante, dapibus in, viverra quis, feugiat a, tellus. Phasellus viverra nulla ut metus varius laoreet. Quisque rutrum. Aenean imperdiet. Etiam ultricies nisi vel augue.</p>
  <div class="read-more">READ MORE &gt;&gt;</div>
  <div class="partner" style="top:220px"><i></i>Studwise</div>
  <div class="partner" style="top:305px"><i></i>Figtrade</div>

  <div class="foot-mark"><i></i>Quarvelnook</div>
  <p class="copy">Copyright ©2016 <b>quarvelnook.example</b>, all rights reserved.<br>BRIXO® is a registered trademark of The BRIXO Group, who has no connection with Quarvelnook whatsoever.</p>
</footer>

</body>
</html>
```